Volbrey Inc Business Card

Looking to get an updated business card for a Contract Machining company (www.volbreyinc.example) - looking for a clean design the portrays the technical nature of the business - colors can follow the website design and be in any combination that makes sense (red black, white, metallic or silver) - logos attached for use also. Would like space for: Name, title, business phone (555 214-3086), cell phone , website (www.volbreyinc.example) - possibly QR code could be integrated for website (designer choice), business address - 418 Harlow Bend, Westhollow, KV 48199 (cards will be for 4 employees, I will either need to modify a template or I can provide individual information)
Target Market(s)
Aerospace, defense and medical device manufacturing companies that need machining
Industry/Entity Type
Machining for aerospace, defense, medical
Contact Information for Business Card
Name, Title, Business Phone, Cell Phone, email, business website and business address
Look and feel

```html
<!DOCTYPE html>
<html lang="en">
<head>
<meta charset="utf-8">
<title>Volbrey Inc Business Card</title>
<link href="https://fonts.googleapis.com/css2?family=Arimo:wght@400;700&display=swap" rel="stylesheet">
<style>
  :root {
    --backdrop: #3d3d3d;
    --brand-red: #b01f24;
    --card-white: #ffffff;
    --ink-light: #ffffff;
  }
  * { margin: 0; padding: 0; box-sizing: border-box; }
  html, body {
    width: 1200px; height: 803px; overflow: hidden;
    background: var(--backdrop);
    font-family: "Arimo", Arial, sans-serif;
  }
  .canvas { position: relative; width: 1200px; height: 803px; }
  .card {
    position: absolute;
    width: 490px; height: 280px;
    border-radius: 18px;
    box-shadow: 0 14px 30px rgba(0,0,0,0.35);
  }
  .card--contact {
    left: 70px; top: 150px;
    background: var(--brand-red);
    color: var(--ink-light);
    display: flex; align-items: center; justify-content: center;
  }
  .card--brand {
    left: 640px; top: 373px;
    background: var(--card-white);
    display: flex; flex-direction: column; align-items: center; justify-content: center;
  }
  .identity { text-align: right; padding-right: 16px; }
  .identity__name { font-weight: 700; font-size: 22px; line-height: 1.1; }
  .identity__title { font-size: 12px; margin-top: 3px; }
  .identity__address { font-size: 12px; margin-top: 8px; line-height: 1.35; }
  .divider { width: 1px; height: 58px; background: rgba(255,255,255,0.75); }
  .contact-list { list-style: none; padding-left: 14px; font-size: 12px; line-height: 1.5; }
  .contact-list li { display: flex; align-items: center; gap: 7px; }
  .contact-list svg { width: 10px; height: 10px; flex: none; }
  .brand-mark {
    width: 120px; height: 120px; border-radius: 50%;
    background: var(--brand-red);
  }
  .brand-name {
    margin-top: 10px;
    color: var(--brand-red);
    font-weight: 700; font-size: 26px; letter-spacing: 1px;
  }
</style>
</head>
<body>
<main class="canvas">
  <section class="card card--contact">
    <div class="identity">
      <div class="identity__name">Daniel Reyes</div>
      <div class="identity__title">President</div>
      <div class="identity__address">418 Harlow Bend<br>Westhollow, KV 48199</div>
    </div>
    <div class="divider"></div>
    <ul class="contact-list">
      <li><svg viewBox="0 0 10 10"><path d="M2 0.5 L3.8 2.6 L2.9 3.6 Q4 5.9 6.4 7.1 L7.4 6.2 L9.5 8 L8.3 9.5 Q3.5 9 0.5 2 Z" fill="#fff"/></svg>555 214-3086</li>
      <li><svg viewBox="0 0 10 10"><rect x="2" y="0.5" width="6" height="9" rx="1" fill="none" stroke="#fff" stroke-width="1"/></svg>555 738-4402</li>
      <li><svg viewBox="0 0 10 10"><rect x="0.5" y="1.5" width="9" height="7" fill="#fff"/><path d="M0.8 2 L5 5.5 L9.2 2" fill="none" stroke="#b01f24" stroke-width="1"/></svg>info@volbreyinc.example</li>
      <li><svg viewBox="0 0 10 10"><circle cx="5" cy="5" r="4.3" fill="none" stroke="#fff" stroke-width="1"/><path d="M0.7 5 H9.3 M5 0.7 Q2.5 5 5 9.3 M5 0.7 Q7.5 5 5 9.3" fill="none" stroke="#fff" stroke-width="0.8"/></svg>www.volbreyinc.example</li>
    </ul>
  </section>

  <section class="card card--brand">
    <div class="brand-mark" role="img" aria-label="Plain circle beside company name"></div>
    <div class="brand-name">VOLBREY INC.</div>
  </section>
</main>
</body>
</html>
```